Business Card Design

Business Card for professional consulting firm working with large financial institutions.

Target Market(s)

Executive buyers

Industry/Entity Type

Banking

Contact Information for Business Card

Mild creativity wanted. Not boring, but do elaborate artwork.

Font styles to use
Serif
Sans Serif

Colors

Designer to choose colors to be used in the design.

Requirements
Must have
• Standard business card features - company name, individual name, telephone, website, email, locations.
Nice to have
• Two colors
Should not have
• too many colors, fancy printing, cartoons.

```html
<!DOCTYPE html>
<html lang="en">
<head>
<meta charset="utf-8">
<title>Northvale Business Card</title>
<link rel="stylesheet" href="https://fonts.googleapis.com/css2?family=Roboto:wght@400;500&family=Roboto+Condensed:wght@500&display=swap">
<style>
  :root {
    --bg: #c9c9c9;
    --paper: #f3f3f3;
    --ink: #111111;
    --text: #3a3a3a;
    --muted: #9a9a9a;
    --rule: #bdbdbd;
    --band-grey: #c4c4c4;
    --white: #ffffff;
    --shadow: rgba(0, 0, 0, 0.28);
  }
  * { box-sizing: border-box; margin: 0; padding: 0; }
  html, body {
    width: 1200px; height: 960px; overflow: hidden;
    background: var(--bg);
    font-family: "Roboto", Arial, sans-serif;
  }
  .canvas { position: relative; width: 1200px; height: 960px; }

  .card {
    position: absolute; left: 320px; width: 600px; height: 342px;
    box-shadow: 0 3px 8px var(--shadow);
    overflow: hidden;
  }

  /* Front */
  .card-front { top: 100px; background: var(--paper); }
  .front-band { position: absolute; left: 0; bottom: 0; width: 600px; height: 22px; }
  .front-wordmark {
    position: absolute; left: 55px; top: 156px; width: 260px;
    display: flex; align-items: center; justify-content: center; gap: 10px;
    font-size: 30px; font-weight: 400; color: var(--text); letter-spacing: 0.5px;
  }
  .mark-dot { width: 10px; height: 10px; border-radius: 50%; background: var(--muted); }
  .divider {
    position: absolute; left: 347px; top: 95px; width: 1px; height: 155px;
    background: var(--rule);
  }
  .contact { position: absolute; left: 378px; top: 92px; color: var(--text); }
  .contact-name {
    font-family: "Roboto Condensed", "Arial Narrow", sans-serif;
    font-weight: 500; font-size: 21px; color: var(--ink); line-height: 24px;
  }
  .contact-title {
    font-family: "Roboto Condensed", "Arial Narrow", sans-serif;
    font-size: 15px; color: var(--muted); letter-spacing: 0.3px; line-height: 20px;
  }
  .contact-address { margin-top: 10px; font-size: 14px; line-height: 18px; }
  .contact-lines { margin-top: 12px; list-style: none; font-size: 14px; line-height: 19.5px; }
  .contact-lines li { display: flex; align-items: center; gap: 7px; }
  .contact-lines svg { width: 13px; height: 13px; fill: var(--ink); flex: none; }

  /* Back */
  .card-back { top: 493px; background: var(--ink); color: var(--white); }
  .back-wordmark {
    position: absolute; left: 0; right: 0; top: 144px;
    display: flex; align-items: center; justify-content: center; gap: 12px;
    font-size: 36px; font-weight: 400; letter-spacing: 0.5px;
  }
  .back-wordmark .mark-dot { width: 12px; height: 12px; background: var(--white); }
  .back-url {
    position: absolute; left: 0; right: 0; top: 280px; text-align: center;
    font-size: 13px; letter-spacing: 5px;
  }
</style>
</head>
<body>
<main class="canvas">
  <section class="card card-front" aria-label="Business card front">
    <div class="front-wordmark"><span class="mark-dot"></span><span>Northvale</span></div>
    <div class="divider"></div>
    <div class="contact">
      <p class="contact-name">DANIEL REYES</p>
      <p class="contact-title">CEO/FOUNDER</p>
      <p class="contact-address">4120 Harbor View Road<br>Juneau, Alaska 99801</p>
      <ul class="contact-lines">
        <li><svg viewBox="0 0 24 24"><path d="M6.6 10.8a15.1 15.1 0 0 0 6.6 6.6l2.2-2.2c.3-.3.7-.4 1-.2 1.1.4 2.3.6 3.6.6.6 0 1 .4 1 1V20c0 .6-.4 1-1 1A17 17 0 0 1 3 4c0-.6.4-1 1-1h3.5c.6 0 1 .4 1 1 0 1.3.2 2.5.6 3.6.1.3 0 .7-.2 1z"/></svg>555 210 4471</li>
        <li><svg viewBox="0 0 24 24"><path d="M2 5h20v14H2zM4 7v.5l8 5 8-5V7l-8 5z"/></svg>info@northvale.com</li>
        <li><svg viewBox="0 0 24 24"><circle cx="12" cy="12" r="10"/><path d="M12 2v20M2 12h20" stroke="#f3f3f3" stroke-width="1.6"/></svg>www.northvale.com</li>
      </ul>
    </div>
    <svg class="front-band" viewBox="0 0 600 22" aria-hidden="true">
      <rect x="0" y="0" width="600" height="22" fill="var(--band-grey)"/>
      <polygon points="0,0 395,0 388,22 0,22" fill="var(--ink)"/>
    </svg>
  </section>

  <section class="card card-back" aria-label="Business card back">
    <div class="back-wordmark"><span class="mark-dot"></span><span>Northvale</span></div>
    <p class="back-url">www.northvale.com</p>
  </section>
</main>
</body>
</html>
```